Company that sells high quality boat cleaning supplies needs new Homepage Design

We need a homepage design for a company that sells high quality boat cleaning and maintanence products. This company is called VPX61. There are 3 primary products; a soap for boats, waterless wash & Wax, and a Ceramic Spray coating and protectant.

Current Website: https://vpx61.com/

Customer Avatar/ Core Message Canvas: https://sheets.tarvolin.net/s/7qWk2Lp9RbXe4TnHy8MfC3uZaD1oJv6GsKxE5iBtN0Ph/view?share=open

Homepage Template: https://sheets.tarvolin.net/d/4Hb8nYc2QwLe6RkT0vMxJ5aPfZ9uGtSoDi3Ck7EyBn1V/view?share=open

There is info on imagery in the homepage template. Where there isn't, appropriate stock imagery is acceptable.

Logo Design and Slogan images: https://vault.tarvolin.net/f/9kLmQ2rTz8WyHn4PcVb6XeJ0gA5sDu7?share=open

Product Images: https://vault.tarvolin.net/f/3pNcR7wYh1KeTm8ZsVa4QbLu6Dj9Fgx?share=open

```html
<!DOCTYPE html>
<html lang="en">
<head>
<meta charset="utf-8">
<title>VPX61 – Stress-Free Boat Care</title>
<link rel="stylesheet" href="https://fonts.googleapis.com/css2?family=Poppins:ital,wght@0,400;0,500;0,600;0,700;1,400&display=swap">
<style>
:root{
  --cyan:#13a9d3;
  --ink:#111418;
  --muted:#4a4f55;
  --soft:#e9f7fb;
  --hero-a:#0a2a40;
  --hero-b:#123e58;
  --footer:#1b1d1f;
  --line:#33373b;
  --white:#ffffff;
}
*{box-sizing:border-box;margin:0;padding:0}
html,body{width:1200px;height:3449px;overflow:hidden}
body{position:relative;font-family:'Poppins',sans-serif;color:var(--ink);background:var(--white)}
.abs{position:absolute}
.btn{position:absolute;display:flex;align-items:center;justify-content:center;gap:6px;border-radius:5px;font-size:14px;font-weight:500;background:var(--cyan);color:var(--white);text-decoration:none}
.btn-outline{background:transparent;border:1.5px solid var(--cyan);color:var(--cyan)}
.cyan{color:var(--cyan)}

/* hero */
.hero{position:absolute;left:0;top:0;width:1200px;height:577px;background:radial-gradient(ellipse at 62% 40%,#2c5e78 0%,var(--hero-b) 30%,var(--hero-a) 75%)}
.brand{position:absolute;font-weight:500;color:var(--white)}
.nav{position:absolute;left:767px;top:26px;display:flex;gap:30px;font-size:14px;color:var(--white)}
.nav-icons{position:absolute;left:1044px;top:28px;display:flex;gap:16px}
.hero h1{position:absolute;left:107px;top:162px;font-size:47px;line-height:60px;font-weight:600;color:var(--white);letter-spacing:0.3px}
.hero .tags{position:absolute;left:107px;top:358px;font-size:20px;color:var(--white);display:flex;gap:18px;align-items:center}
.dot{width:5px;height:5px;border-radius:50%;background:var(--cyan);display:inline-block}

/* features */
.features{position:absolute;left:0;top:577px;width:1200px;height:150px;background:var(--soft)}
.feature{position:absolute;top:26px;width:200px;margin-left:-100px;text-align:center;font-size:14px;font-weight:600;line-height:20px}
.feature svg{display:block;margin:0 auto 14px}

/* products */
.media{position:absolute;border-radius:2px}
.product h2{position:absolute;font-size:46px;line-height:60px;font-weight:600}
.product p{position:absolute;font-size:14px;line-height:27px;color:var(--muted);width:405px}

/* community card */
.card-news{position:absolute;left:189px;top:1634px;width:822px;height:274px;background:var(--soft);border-radius:40px;box-shadow:0 6px 18px rgba(19,169,211,.12)}
.card-news h3{position:absolute;left:63px;top:28px;font-size:31px;line-height:45px;font-weight:600}
.card-news p{position:absolute;left:63px;top:142px;font-size:14px;color:var(--muted)}
.subscribe{position:absolute;left:63px;top:198px;width:696px;height:40px;background:var(--white);border-radius:6px;display:flex;overflow:hidden}
.subscribe span{flex:1;padding-left:20px;line-height:40px;font-size:14px;color:#9aa0a6}
.subscribe b{width:110px;background:var(--cyan);color:var(--white);font-weight:500;font-size:14px;display:flex;align-items:center;justify-content:center}

/* solution */
.solution-title{position:absolute;left:0;top:2368px;width:1200px;text-align:center;font-size:46px;font-weight:600}
.solution-sub{position:absolute;left:0;top:2442px;width:1200px;text-align:center;font-size:14px;color:var(--muted)}
.post{position:absolute;top:2496px;width:321px;height:352px;background:var(--white);border-radius:8px;box-shadow:0 4px 16px rgba(0,0,0,.09);overflow:hidden}
.post .thumb{height:217px}
.post .date{position:absolute;left:26px;top:230px;font-size:12px;font-style:italic;color:var(--cyan);display:flex;gap:6px;align-items:center}
.post h4{position:absolute;left:26px;top:252px;font-size:14px;font-weight:600}
.post p{position:absolute;left:26px;top:282px;width:280px;font-size:14px;line-height:27px;color:var(--muted)}

/* signup band */
.signup{position:absolute;left:0;top:3011px;width:1200px;height:149px;background:var(--soft)}
.signup h3{position:absolute;left:107px;top:38px;font-size:32px;font-weight:600}
.signup p{position:absolute;left:107px;top:88px;font-size:14px;color:var(--muted)}

/* footer */
.footer{position:absolute;left:0;top:3160px;width:1200px;height:289px;background:var(--footer);color:#cfd3d6}
.footer h5{position:absolute;top:32px;font-size:19px;font-weight:500;color:var(--cyan)}
.footer ul{position:absolute;top:78px;list-style:none;font-size:14px;line-height:33.5px}
.footer .legal{position:absolute;left:107px;top:179px;font-size:14px;display:flex;gap:14px;align-items:center}
.contact{position:absolute;left:880px;top:78px;font-size:14px;line-height:27px}
.contact div{display:flex;gap:20px;margin-bottom:16px}
.contact svg{flex:none;margin-top:5px}
.footer .rule{position:absolute;left:107px;top:248px;width:987px;height:1px;background:var(--line)}
.footer .copy{position:absolute;left:107px;top:259px;font-size:14px}
.social{position:absolute;left:976px;top:262px;display:flex;gap:22px}
.social i{width:13px;height:13px;border-radius:50%;background:#e6e8ea;display:block}
</style>
</head>
<body>

<header class="hero">
  <div role="img" aria-label="Aerial photo of a speedboat carving a white wake across dark blue water" class="abs" style="left:0;top:0;width:1200px;height:577px;background:radial-gradient(ellipse 26% 48% at 63% 38%,rgba(230,240,245,.22),transparent 70%)"></div>
  <div class="brand" style="left:107px;top:22px;font-size:24px">VPX61</div>
  <nav class="nav"><span>Home</span><span>Shop</span><span>Blog</span><span>Contact</span></nav>
  <div class="nav-icons">
    <svg width="18" height="18" viewBox="0 0 18 18" fill="none" stroke="#fff" stroke-width="1.4"><path d="M1 2h3l2 9h9l2-6H5"/><circle cx="7" cy="15" r="1.3"/><circle cx="14" cy="15" r="1.3"/></svg>
    <svg width="18" height="18" viewBox="0 0 18 18" fill="none" stroke="#fff" stroke-width="1.4"><circle cx="9" cy="6" r="3.5"/><path d="M2 17c1-4 4-5.5 7-5.5s6 1.5 7 5.5"/></svg>
  </div>
  <h1>Stress-Free Boat Care:<br>VPX61 Takes The Hard Work<br>Out of Cleaning &amp; Detailing</h1>
  <div class="tags"><span>ECO Friendly</span><i class="dot"></i><span>Simple Application</span><i class="dot"></i><span>Advanced Nanotechnolgies</span></div>
  <a class="btn btn-outline" style="left:107px;top:408px;width:102px;height:38px">Our Blog</a>
  <a class="btn" style="left:225px;top:408px;width:125px;height:38px">Shop VPX61</a>
</header>

<section class="features">
  <div class="feature" style="left:161px">
    <svg width="48" height="48" viewBox="0 0 48 48" fill="none" stroke="var(--cyan)" stroke-width="2"><circle cx="24" cy="24" r="21"/><circle cx="24" cy="24" r="13"/><circle cx="24" cy="24" r="5"/><path d="M24 24l14-14M33 10h5v5"/></svg>
    Simple<br>Application</div>
  <div class="feature" style="left:375px">
    <svg width="60" height="48" viewBox="0 0 60 48" fill="none" stroke="var(--cyan)" stroke-width="2"><path d="M4 12h22l6 3h22l-3 10 3 6-10 8-6-2-8 4-6-4H10L4 28z"/><path d="M6 18h44M6 24h44M6 30h40"/></svg>
    Made in<br>the USA</div>
  <div class="feature" style="left:573px">
    <svg width="48" height="48" viewBox="0 0 48 48" fill="none" stroke="var(--cyan)" stroke-width="2"><circle cx="24" cy="20" r="12"/><text x="24" y="23" font-size="8" font-family="Poppins,sans-serif" fill="var(--cyan)" stroke="none" text-anchor="middle">ECO</text><path d="M8 44c0-10 6-14 12-14-1 8-6 12-12 14zM40 44c0-10-6-14-12-14 1 8 6 12 12 14z"/></svg>
    Eco<br>Friendly</div>
  <div class="feature" style="left:803px">
    <svg width="48" height="48" viewBox="0 0 48 48" fill="none" stroke="var(--cyan)" stroke-width="2"><path d="M24 2v44M5 13l38 22M43 13L5 35"/><path d="M19 5l5 5 5-5M19 43l5-5 5 5M6 20l7-2-2-7M42 28l-7 2 2 7M42 20l-7-2 2-7M6 28l7 2-2 7"/></svg>
    Designed for any<br>conditions</div>
  <div class="feature" style="left:1044px">
    <svg width="52" height="48" viewBox="0 0 52 48" fill="none" stroke="var(--cyan)" stroke-width="2"><path d="M26 2l6 5 8-1 2 8 7 5-4 7 3 8-8 3-2 8-8-1-6 5-6-5-8 1-2-8-8-3 3-8-4-7 7-5 2-8 8 1z"/><path d="M17 24l6 6 12-12"/></svg>
    Works the<br>First Time</div>
</section>

<section class="product">
  <h2 style="left:106px;top:856px">Waterless<br><span class="cyan">Wash &amp; Wax</span></h2>
  <p style="left:106px;top:992px">Amet consectetur. Pharetra nulla suscipit hendrerit velit sed. Viverra egestas ullamcorper purus pretium adipiscing.</p>
  <a class="btn" style="left:106px;top:1070px;width:138px;height:37px">Add To Cart
    <svg width="15" height="14" viewBox="0 0 18 18" fill="none" stroke="#fff" stroke-width="1.6"><path d="M1 2h3l2 9h9l2-6H5"/><circle cx="7" cy="15" r="1.3"/><circle cx="14" cy="15" r="1.3"/></svg></a>
  <div class="media" role="img" aria-label="Video still: a hand spraying waterless wash onto a white boat hull beside a porthole" style="left:608px;top:818px;width:485px;height:335px;background:linear-gradient(135deg,#c9cbcc,#8d9092 55%,#5b5e60)"></div>
  <svg class="abs" style="left:796px;top:926px" width="120" height="120" viewBox="0 0 120 120"><circle cx="60" cy="60" r="58" fill="rgba(255,255,255,.35)"/><circle cx="60" cy="60" r="44" fill="#fff"/><path d="M52 45l22 15-22 15z" fill="#111"/></svg>
</section>

<section class="product">
  <div class="media" role="img" aria-label="Video still: a gloved hand applying ceramic spray coating with a pump sprayer on a boat deck" style="left:63px;top:1244px;width:447px;height:298px;background:linear-gradient(135deg,#e7e8e3,#b3b5ae 50%,#55574f)"></div>
  <svg class="abs" style="left:212px;top:1330px" width="120" height="120" viewBox="0 0 120 120"><circle cx="60" cy="60" r="58" fill="rgba(255,255,255,.35)"/><circle cx="60" cy="60" r="44" fill="#fff"/><path d="M52 45l22 15-22 15z" fill="#111"/></svg>
  <h2 style="left:609px;top:1235px"><span class="cyan">Graphene Ceramic</span><br>Spray Coating and<br>Protectant</h2>
  <p style="left:609px;top:1428px">Amet consectetur. Pharetra nulla suscipit hendrerit velit sed. Viverra egestas ullamcorper purus pretium adipiscing.</p>
  <a class="btn" style="left:609px;top:1505px;width:138px;height:38px">Add To Cart
    <svg width="15" height="14" viewBox="0 0 18 18" fill="none" stroke="#fff" stroke-width="1.6"><path d="M1 2h3l2 9h9l2-6H5"/><circle cx="7" cy="15" r="1.3"/><circle cx="14" cy="15" r="1.3"/></svg></a>
</section>

<section class="card-news">
  <h3><span class="cyan">Join Our Community</span>: Exclusive Deals,<br>Tips, and Updates Straight to Your Inbox</h3>
  <p>Join today &amp; stay up-to-date on new product releases, shop promotions, and our archery newsletters</p>
  <div class="subscribe"><span>example123@mailbox.test</span><b>Subscribe</b></div>
</section>

<section class="product">
  <h2 style="left:106px;top:2016px"><span class="cyan">Pink Soap</span><br>For Boats</h2>
  <p style="left:106px;top:2141px">Amet consectetur. Pharetra nulla suscipit hendrerit velit sed. Viverra egestas ullamcorper purus pretium adipiscing.</p>
  <a class="btn" style="left:106px;top:2219px;width:138px;height:37px">Add To Cart
    <svg width="15" height="14" viewBox="0 0 18 18" fill="none" stroke="#fff" stroke-width="1.6"><path d="M1 2h3l2 9h9l2-6H5"/><circle cx="7" cy="15" r="1.3"/><circle cx="14" cy="15" r="1.3"/></svg></a>
  <div class="media" role="img" aria-label="Video still: a row of product bottles, soap, waterless wash and spray protectant" style="left:603px;top:1998px;width:490px;height:290px;background:linear-gradient(90deg,#5a2320,#d9d7d2 25%,#efefed 45%,#c9c6c0 65%,#e8e8e6 80%,#9a9894)"></div>
  <svg class="abs" style="left:787px;top:2086px" width="120" height="120" viewBox="0 0 120 120"><circle cx="60" cy="60" r="58" fill="rgba(255,255,255,.35)"/><circle cx="60" cy="60" r="44" fill="#fff"/><path d="M52 45l22 15-22 15z" fill="#111"/></svg>
</section>

<section>
  <h2 class="solution-title">The <span class="cyan">VPX61</span> Solution</h2>
  <p class="solution-sub">Cleaning Products that Work The First Time!</p>

  <article class="post" style="left:107px">
    <div class="thumb" role="img" aria-label="Aerial photo of a motor yacht speeding through deep blue sea" style="background:linear-gradient(135deg,#0d4d7a,#1f6fa0 50%,#0a3d63)"></div>
    <span class="date"><svg width="12" height="12" viewBox="0 0 12 12" fill="none" stroke="var(--cyan)"><rect x="1" y="2" width="10" height="9" rx="1"/><path d="M1 5h10M4 1v2M8 1v2"/></svg>July 22, 2022</span>
    <h4>What's the Best Boat Wax?</h4>
    <p>We feel that a well-formulated, properly applied sprayable ceramic....</p>
  </article>
  <article class="post" style="left:439px">
    <div class="thumb" role="img" aria-label="Photo of a gloved hand wiping a wooden boat steering wheel" style="background:linear-gradient(135deg,#2a2c2e,#6b6e70 50%,#8a6a44)"></div>
    <span class="date"><svg width="12" height="12" viewBox="0 0 12 12" fill="none" stroke="var(--cyan)"><rect x="1" y="2" width="10" height="9" rx="1"/><path d="M1 5h10M4 1v2M8 1v2"/></svg>July 22, 2022</span>
    <h4>Why Use a Waterless Wash &amp; Wax?</h4>
    <p>Convenience! Waterless wash and wax products are the "new wave" of....</p>
  </article>
  <article class="post" style="left:773px">
    <div class="thumb" role="img" aria-label="Photo of white boats moored in a marina at sunset" style="background:linear-gradient(180deg,#c7a98a,#9fa4a7 50%,#4b5a63)"></div>
    <span class="date"><svg width="12" height="12" viewBox="0 0 12 12" fill="none" stroke="var(--cyan)"><rect x="1" y="2" width="10" height="9" rx="1"/><path d="M1 5h10M4 1v2M8 1v2"/></svg>July 22, 2022</span>
    <h4>What Should I Wash My Boat With?</h4>
    <p>There are a lot of Harsh cleaners out there which is why we created....</p>
  </article>

  <a class="btn" style="left:501px;top:2883px;width:198px;height:37px">Read our Blog for More</a>
</section>

<section class="signup">
  <h3>Join Our Community By Signing Up Now</h3>
  <p>Join today &amp; stay up-to-date on new product releases, shop promotions, and our archery newsletters</p>
  <a class="btn" style="left:998px;top:57px;width:96px;height:36px">Sign Up</a>
</section>

<footer class="footer">
  <div class="brand" style="left:107px;top:58px;font-size:62px;font-weight:600">VPX61</div>
  <div class="legal"><span>Terms Of Service</span><i class="dot"></i><span>Privacy Policy</span></div>

  <h5 style="left:424px">Quick Links</h5>
  <ul style="left:424px"><li>Home</li><li>Shop</li><li>Blog</li><li>Contact</li></ul>

  <h5 style="left:623px">Case Studies</h5>
  <ul style="left:623px"><li>Pharetra nulla</li><li>dui consequat</li><li>Best Boat Wax</li><li>Waterless Wash &amp; Wax</li></ul>

  <h5 style="left:880px">Contact Us</h5>
  <div class="contact">
    <div><svg width="14" height="16" viewBox="0 0 14 16" fill="var(--cyan)"><path d="M7 0a6 6 0 016 6c0 4.5-6 10-6 10S1 10.5 1 6a6 6 0 016-6z"/><circle cx="7" cy="6" r="2" fill="var(--footer)"/></svg><span>Ipsum dolor sit amet<br>Massa nulla amet</span></div>
    <div><svg width="14" height="16" viewBox="0 0 14 16" fill="var(--cyan)"><rect x="3" y="0" width="8" height="16" rx="1.5"/><rect x="4.5" y="2" width="5" height="10" fill="var(--footer)"/></svg><span>098-555-0142</span></div>
    <div><svg width="14" height="14" viewBox="0 0 14 14" fill="var(--cyan)"><rect x="0" y="2" width="14" height="10" rx="1"/><path d="M1 3l6 5 6-5" stroke="var(--footer)" stroke-width="1.3" fill="none"/></svg><span>hello@vpx61-mail.test</span></div>
  </div>

  <div class="rule"></div>
  <div class="copy">© Copyright 2023 All rights received</div>
  <div class="social"><i></i><i></i><i></i><i></i></div>
</footer>

</body>
</html>
```